Etikett für Rotweinflasche
Liebe farbkosmos Atelier, wir werden uns bei der endgültigen Etikettengestaltung (finale Größe + Rückseite) noch an Euch melden. Bitte sendet uns euren Kontakt an helga.brandt@morvelli.wine
Zielgruppe
Morvelli Italia ist ein exklusives Boutique-Weingut in Sizilien, das hochqualitative Spitzenweine in kleinen Mengen mit modernster Technologie und stets nachhaltig erzeugt. Wir hinterfragen sowohl in der Agronomie im Weingarten als auch in der Önologie im Weinkeller alle herrschenden Traditionen und trachten danach, stets das beste Endprodukt zu kreieren. Der vulkanische, kalkreiche Boden Siziliens sowie trockene, sonnenreiche und niederschlagsarme Vegetationsperioden sind unsere optimale Basis.
Zielgruppe: Internationale Genussmenschen jeglichen Alters, die sich bewusst auch höherpreisige Weine (um die €30+) gönnen , vor allem kunstaffine young professionals mit Qualitäts-& Nachhaltigkeitsanspruch
Aufgabenstellung
Das Etikett ist für Rotwein-Flaschen (Cabernet Sauvignon / Nero D'Avola / Frappato / Syrah / Cerasuolo / Petit Verdot / sowie einen Bourdeaux-Cuveè aus Cabernet Sauvignon und Petit Verdot) .
Die Flasche ist reinschwarz, sehr hochwertig und schwer.
Flaschenform: Bordeauxflasche siehe technisches Datenblatt
Sleeve über dem Korken: schwarz mit weißer Schrift wie bisher
Zu gestalten ist das Etikett der Vorderseite. Zumindest die jeweilige Rotwein-Sorte ist auch textlich darzustellen (zwecks Scannen mit Trubel-App)
Der Kreativität kann freien Lauf gelassen werden! Unterscheidbarkeit vom Markt ist explizit gewollt.
Unsere aktuellen Etiketten und Markenauftritt siehe: https://morvelli.wine/shop/

```html
<!DOCTYPE html>
<html lang="it">
<head>
<meta charset="utf-8">
<title>Cabernet Sauvignon – Etikett</title>
<link rel="stylesheet" href="https://fonts.googleapis.com/css2?family=Big+Shoulders+Text:wght@300&display=swap">
<style>
  :root {
    --label-cream: #ecdcb9;
    --ink: #1c1a17;
    --owl-navy: #141a2a;
    --owl-blue: #22385c;
    --owl-teal: #1f6a62;
    --owl-green: #3fa070;
    --owl-plum: #2a2740;
    --owl-amber: #c8721e;
  }
  html, body {
    margin: 0;
    padding: 0;
    width: 849px;
    height: 1200px;
    overflow: hidden;
    background: var(--label-cream);
  }
  .wine-label {
    position: relative;
    width: 849px;
    height: 1200px;
    background: var(--label-cream);
    overflow: hidden;
  }
  .varietal-name {
    position: absolute;
    top: 30px;
    left: 0;
    width: 100%;
    margin: 0;
    text-align: center;
    font-family: "Big Shoulders Text", "Arial Narrow", sans-serif;
    font-weight: 300;
    font-size: 40px;
    letter-spacing: 0.3em;
    color: var(--ink);
    line-height: 1;
  }
  .owl-artwork {
    position: absolute;
    top: 80px;
    left: 0;
    width: 849px;
    height: 1120px;
    display: block;
  }
</style>
</head>
<body>
  <main class="wine-label">
    <h1 class="varietal-name">CABERNET SAUVIGNON</h1>
    <svg class="owl-artwork" role="img" aria-label="Illustration: frontal painted owl with large round eyes and scaled feathers in navy, teal, green and amber tones" viewBox="0 0 849 1120">
      <defs>
        <linearGradient id="owl-body-tones" x1="0" y1="0" x2="0" y2="1">
          <stop offset="0" stop-color="var(--owl-navy)"/>
          <stop offset="0.3" stop-color="var(--owl-blue)"/>
          <stop offset="0.55" stop-color="var(--owl-teal)"/>
          <stop offset="0.78" stop-color="var(--owl-plum)"/>
          <stop offset="1" stop-color="var(--owl-amber)"/>
        </linearGradient>
        <radialGradient id="owl-chest-glow" cx="0.5" cy="0.6" r="0.45">
          <stop offset="0" stop-color="var(--owl-green)" stop-opacity="0.95"/>
          <stop offset="1" stop-color="var(--owl-green)" stop-opacity="0"/>
        </radialGradient>
        <radialGradient id="owl-base-glow" cx="0.5" cy="1" r="0.5">
          <stop offset="0" stop-color="var(--owl-amber)" stop-opacity="0.9"/>
          <stop offset="1" stop-color="var(--owl-amber)" stop-opacity="0"/>
        </radialGradient>
        <radialGradient id="owl-edge-shade" cx="0.5" cy="0.55" r="0.7">
          <stop offset="0.6" stop-color="var(--owl-navy)" stop-opacity="0"/>
          <stop offset="1" stop-color="var(--owl-navy)" stop-opacity="0.7"/>
        </radialGradient>
        <clipPath id="owl-silhouette">
          <path d="M0 260 C 60 130, 240 60, 424 60 C 610 60, 790 130, 849 260 L 849 1120 L 0 1120 Z"/>
        </clipPath>
      </defs>
      <g clip-path="url(#owl-silhouette)">
        <rect x="0" y="0" width="849" height="1120" fill="url(#owl-body-tones)"/>
        <rect x="0" y="0" width="849" height="1120" fill="url(#owl-chest-glow)"/>
        <rect x="0" y="0" width="849" height="1120" fill="url(#owl-base-glow)"/>
        <rect x="0" y="0" width="849" height="1120" fill="url(#owl-edge-shade)"/>
      </g>
    </svg>
  </main>
</body>
</html>
```